Briefpapier und Visitenkarten
Zielgruppe
In erster Linie mir selbst.
Aufgabenstellung
Gestaltung von Visitenkarten und Briefpapier.
Visitenkarten: Gestaltung beidseitig und in Pantone Farben
Briefpapier: Gestaltung einseitig und in Pantone Farben
Briefpapier und Visitenkarten sollen ein Design haben.

```html
<!DOCTYPE html>
<html lang="de">
<head>
<meta charset="utf-8">
<title>Korlan Werbeagentur – Visitenkarten</title>
<link href="https://fonts.googleapis.com/css2?family=Arimo:wght@400;700&display=swap" rel="stylesheet">
<style>
  :root {
    --backdrop: #4a4a4c;
    --card-grey: #c4c4c6;
    --card-white: #ffffff;
    --ink-on-grey: #ffffff;
    --ink-on-white: #b3b3b5;
    --deco-on-grey: #cdcdcf;
    --deco-on-white: #f3f3f4;
  }
  html, body {
    margin: 0;
    padding: 0;
    width: 1200px;
    height: 1200px;
    overflow: hidden;
    background: var(--backdrop);
    font-family: "Arimo", Arial, sans-serif;
  }
  .sheet { position: relative; width: 1200px; height: 1200px; }

  .card {
    position: absolute;
    width: 475px;
    height: 307px;
    border-radius: 23px;
    overflow: hidden;
    box-shadow: 0 4px 10px rgba(0,0,0,0.35);
  }
  .card--white { background: var(--card-white); color: var(--ink-on-white); --deco: var(--deco-on-white); }
  .card--grey  { background: var(--card-grey);  color: var(--ink-on-grey);  --deco: var(--deco-on-grey); }

  .card--back-white  { left: 88px;  top: 105px; }
  .card--back-grey   { left: 637px; top: 105px; }
  .card--front-grey  { left: 88px;  top: 480px; }
  .card--front-white { left: 637px; top: 480px; }

  .deco-circle {
    position: absolute;
    left: 3px;
    top: 98px;
    width: 234px;
    height: 234px;
    border-radius: 50%;
    background: var(--deco);
  }

  .brand {
    position: absolute;
    left: 0;
    right: 0;
    text-align: center;
  }
  .card--back-white .brand, .card--back-grey .brand { top: 92px; }
  .card--front-grey .brand, .card--front-white .brand { top: 18px; }

  .brand__dot {
    display: block;
    width: 50px;
    height: 50px;
    margin: 0 auto 8px;
    border-radius: 50%;
    background: currentColor;
  }
  .brand__name {
    font-weight: 700;
    font-size: 18px;
    letter-spacing: 0.5px;
    line-height: 20px;
    text-transform: uppercase;
  }
  .brand__tagline {
    font-size: 7px;
    letter-spacing: 3.4px;
    line-height: 10px;
    margin-top: 2px;
    text-transform: uppercase;
  }

  .person {
    position: absolute;
    left: 20px;
    top: 125px;
  }
  .person__name { font-weight: 700; font-size: 15px; line-height: 18px; }
  .person__role { font-size: 11px; line-height: 13px; }

  .contact {
    position: absolute;
    left: 282px;
    top: 155px;
    font-size: 11px;
    line-height: 13.5px;
    letter-spacing: 0.2px;
  }
  .contact p { margin: 0; }
  .contact__group + .contact__group { margin-top: 5px; }
  .contact__company, .contact__web { font-weight: 700; }
  .contact__label { display: inline-block; width: 36px; }
</style>
</head>
<body>
<main class="sheet">

  <section class="card card--white card--back-white" aria-label="Rückseite weiß">
    <div class="deco-circle"></div>
    <div class="brand">
      <span class="brand__dot"></span>
      <div class="brand__name">Korlan Werbeagentur</div>
      <div class="brand__tagline">Ideen mit Wirkung</div>
    </div>
  </section>

  <section class="card card--grey card--back-grey" aria-label="Rückseite grau">
    <div class="deco-circle"></div>
    <div class="brand">
      <span class="brand__dot"></span>
      <div class="brand__name">Korlan Werbeagentur</div>
      <div class="brand__tagline">Ideen mit Wirkung</div>
    </div>
  </section>

  <section class="card card--grey card--front-grey" aria-label="Vorderseite grau">
    <div class="deco-circle"></div>
    <div class="brand">
      <span class="brand__dot"></span>
      <div class="brand__name">Korlan Werbeagentur</div>
      <div class="brand__tagline">Ideen mit Wirkung</div>
    </div>
    <div class="person">
      <div class="person__name">Jonas Korlan</div>
      <div class="person__role">Geschäftsführer</div>
    </div>
    <div class="contact">
      <div class="contact__group"><p class="contact__company">Korlan Werbeagentur</p></div>
      <div class="contact__group"><p>Lindenweg 14</p><p>D-53000 Altenfeld</p></div>
      <div class="contact__group">
        <p><span class="contact__label">Fon</span>+49 (0) 4321 98765-11</p>
        <p><span class="contact__label">Fax</span>+49 (0) 4321 98765-99</p>
        <p><span class="contact__label">Mobil</span>+49 (0) 321 9876543</p>
      </div>
      <div class="contact__group"><p>korlan@korlanwa.de</p><p class="contact__web">www.korlanwa.de</p></div>
    </div>
  </section>

  <section class="card card--white card--front-white" aria-label="Vorderseite weiß">
    <div class="deco-circle"></div>
    <div class="brand">
      <span class="brand__dot"></span>
      <div class="brand__name">Korlan Werbeagentur</div>
      <div class="brand__tagline">Ideen mit Wirkung</div>
    </div>
    <div class="person">
      <div class="person__name">Jonas Korlan</div>
      <div class="person__role">Geschäftsführer</div>
    </div>
    <div class="contact">
      <div class="contact__group"><p class="contact__company">Korlan Werbeagentur</p></div>
      <div class="contact__group"><p>Lindenweg 14</p><p>D-53000 Altenfeld</p></div>
      <div class="contact__group">
        <p><span class="contact__label">Fon</span>+49 (0) 4321 98765-11</p>
        <p><span class="contact__label">Fax</span>+49 (0) 4321 98765-99</p>
        <p><span class="contact__label">Mobil</span>+49 (0) 321 9876543</p>
      </div>
      <div class="contact__group"><p>korlan@korlanwa.de</p><p class="contact__web">www.korlanwa.de</p></div>
    </div>
  </section>

</main>
</body>
</html>
```